Harlow Denatl Laboratory nees a window design

We want to make a window cover 8 feet wide and 6 feet tall to advertise our dental lab with all the products we produce<br/>: Digital Cad/Cam<br/>: Implants<br/>: Dentures<br/>: Cast Partials <br/>: Orthodontic appliances<br/><br/> and it has to include a service we provide for a denturist on site by appointment only.<br/><br/>Please use the sample logo below our colours are white backround and blue letters

Font styles to use
Script

Colors
ffffff
0355a3

Requirements
Nice to have
• a picture of a teddy bear on a dental chair, or some dental work particularly bridge work since our moto is Building bridges since 1976
Should not have
• real people

```html
<!DOCTYPE html>
<html lang="en">
<head>
<meta charset="utf-8">
<title>Harlow Dental Laboratory – Window Cover</title>
<link rel="stylesheet" href="https://fonts.googleapis.com/css2?family=Roboto+Condensed:ital,wght@0,300;0,700;1,300;1,700;1,800&display=swap">
<style>
  :root {
    --blue: #2a8bcb;
    --blue-deep: #0355a3;
    --panel: #f2f2f4;
    --white: #ffffff;
    --photo-gum: #d99a9a;
    --photo-tooth: #ece7df;
    --photo-bone: #e3d6c8;
  }
  html, body {
    margin: 0;
    padding: 0;
    overflow: hidden;
    background: var(--white);
  }
  .canvas {
    position: relative;
    width: 1200px;
    height: 900px;
    overflow: hidden;
    background: var(--white);
    font-family: "Roboto Condensed", "Arial Narrow", sans-serif;
    color: var(--blue);
  }
  .backdrop {
    position: absolute;
    inset: 0;
  }
  .brand {
    position: absolute;
    left: 70px;
    top: 52px;
    display: flex;
    align-items: center;
    gap: 22px;
    color: var(--blue);
    font-weight: 700;
  }
  .brand-mark {
    width: 26px;
    height: 26px;
    border-radius: 50%;
    background: var(--blue);
  }
  .brand-name {
    line-height: 1;
  }
  .brand-name .primary {
    display: block;
    font-size: 104px;
    letter-spacing: 4px;
  }
  .brand-name .secondary {
    display: block;
    font-size: 44px;
    letter-spacing: 2px;
    margin-top: 6px;
    padding-left: 40px;
  }
  .tagline {
    position: absolute;
    right: 58px;
    top: 80px;
    margin: 0;
    text-align: right;
    font-weight: 700;
    font-style: italic;
    font-size: 26px;
    line-height: 34px;
    color: var(--blue);
  }
  .products {
    position: absolute;
    left: 68px;
    top: 402px;
  }
  .products-title {
    margin: 0 0 4px;
    font-size: 52px;
    font-weight: 800;
    font-style: italic;
    line-height: 1;
    color: var(--blue);
  }
  .products-list {
    list-style: none;
    margin: 0;
    padding: 0;
  }
  .products-list li {
    font-size: 40px;
    font-weight: 700;
    font-style: italic;
    line-height: 46.5px;
    color: var(--blue);
  }
  .products-list li::before {
    content: "•";
    display: inline-block;
    width: 28px;
  }
  .denturist-band {
    position: absolute;
    left: 0;
    top: 735px;
    width: 715px;
    height: 83px;
    background: linear-gradient(90deg, var(--blue) 0%, var(--blue) 45%, rgba(42,139,203,0.55) 80%, rgba(42,139,203,0) 100%);
    color: var(--white);
    padding-left: 68px;
    box-sizing: border-box;
  }
  .denturist-band .headline {
    display: block;
    font-size: 35px;
    font-weight: 700;
    font-style: italic;
    line-height: 40px;
    padding-top: 6px;
  }
  .denturist-band .note {
    display: block;
    font-size: 28px;
    font-weight: 300;
    font-style: italic;
    line-height: 30px;
  }
  .contact {
    position: absolute;
    left: 66px;
    top: 843px;
    display: flex;
    gap: 26px;
    font-size: 25px;
    font-weight: 700;
    font-style: italic;
    color: var(--blue);
  }
  .contact-item {
    display: flex;
    align-items: center;
    gap: 8px;
  }
  .contact-item svg {
    width: 20px;
    height: 22px;
  }
</style>
</head>
<body>
<div class="canvas">

  <svg class="backdrop" width="1200" height="900" viewBox="0 0 1200 900" xmlns="http://www.w3.org/2000/svg">
    <defs>
      <clipPath id="hero-clip">
        <path d="M670 375 Q 880 200 1200 272 L1200 518 L640 518 Z"/>
      </clipPath>
      <linearGradient id="hero-tone" x1="0" y1="0" x2="0" y2="1">
        <stop offset="0" stop-color="#c9797c"/>
        <stop offset="0.45" stop-color="var(--photo-tooth)"/>
        <stop offset="1" stop-color="var(--photo-bone)"/>
      </linearGradient>
      <linearGradient id="denture-tone" x1="0" y1="0" x2="0" y2="1">
        <stop offset="0" stop-color="#f1b8b4"/>
        <stop offset="0.5" stop-color="#f7f3ee"/>
        <stop offset="1" stop-color="#efc3bd"/>
      </linearGradient>
      <linearGradient id="partial-tone" x1="0" y1="0" x2="1" y2="1">
        <stop offset="0" stop-color="#f6f2ef"/>
        <stop offset="1" stop-color="#efd7cf"/>
      </linearGradient>
      <linearGradient id="bridge-tone" x1="0" y1="0" x2="0" y2="1">
        <stop offset="0" stop-color="#b56d72"/>
        <stop offset="0.5" stop-color="#e9e4dd"/>
        <stop offset="1" stop-color="#c9878a"/>
      </linearGradient>
      <linearGradient id="overdenture-tone" x1="0" y1="0" x2="0" y2="1">
        <stop offset="0" stop-color="#f7f5f2"/>
        <stop offset="0.55" stop-color="#f0c9c3"/>
        <stop offset="1" stop-color="#e7b0aa"/>
      </linearGradient>
    </defs>

    <path class="hero-arc" d="M670 375 Q 880 140 1200 230 L1200 272 Q 880 200 670 375 Z" fill="var(--blue)"/>
    <g role="img" aria-label="Close-up of an implant with a crown placed between natural teeth in the jaw">
      <rect x="640" y="200" width="560" height="318" fill="url(#hero-tone)" clip-path="url(#hero-clip)"/>
    </g>
    <g role="img" aria-label="Full upper and lower acrylic denture set">
      <rect x="640" y="518" width="320" height="210" fill="url(#denture-tone)"/>
    </g>
    <g role="img" aria-label="Flexible partial denture held between fingertips">
      <rect x="960" y="518" width="240" height="210" fill="url(#partial-tone)"/>
    </g>
    <g role="img" aria-label="Implant-supported bridge being seated on two implants">
      <rect x="640" y="728" width="320" height="172" fill="url(#bridge-tone)"/>
    </g>
    <g role="img" aria-label="Overdenture on four implant attachments">
      <rect x="960" y="728" width="240" height="172" fill="url(#overdenture-tone)"/>
    </g>

    <ellipse class="panel-rim" cx="300" cy="1050" rx="480" ry="770" fill="var(--blue)" opacity="0.92"/>
    <ellipse class="panel" cx="300" cy="1050" rx="440" ry="720" fill="var(--panel)"/>
    <ellipse class="panel-line" cx="300" cy="1050" rx="440" ry="720" fill="none" stroke="var(--white)" stroke-width="3"/>
  </svg>

  <div class="brand">
    <span class="brand-mark"></span>
    <span class="brand-name">
      <span class="primary">HARLOW</span>
      <span class="secondary">Dental Laboratory</span>
    </span>
  </div>

  <p class="tagline">BUILDING BRIDGES<br>SINCE 1976</p>

  <section class="products">
    <h2 class="products-title">PRODUCTS</h2>
    <ul class="products-list">
      <li>Digital Cad/Cam</li>
      <li>Implants</li>
      <li>Dentures</li>
      <li>Cast Partials</li>
      <li>Orthodontic appliances</li>
    </ul>
  </section>

  <div class="denturist-band">
    <span class="headline">Denturist on site by appointment</span>
    <span class="note">Walk-ins welcome</span>
  </div>

  <div class="contact">
    <span class="contact-item">
      <svg viewBox="0 0 20 22" aria-hidden="true">
        <path d="M10 1 C5 1 2 4.5 2 8.5 C2 13 10 20 10 20 C10 20 18 13 18 8.5 C18 4.5 15 1 10 1 Z" fill="none" stroke="var(--blue)" stroke-width="2.2"/>
        <circle cx="10" cy="8.5" r="3" fill="none" stroke="var(--blue)" stroke-width="2"/>
        <line x1="3" y1="21" x2="17" y2="21" stroke="var(--blue)" stroke-width="1.8"/>
      </svg>
      2180 Bayview Crescent W.
    </span>
    <span class="contact-item">
      <svg viewBox="0 0 20 22" aria-hidden="true">
        <rect x="1" y="4" width="5" height="16" rx="1" fill="var(--blue)"/>
        <rect x="7" y="7" width="12" height="13" rx="1" fill="none" stroke="var(--blue)" stroke-width="2"/>
        <rect x="9" y="2" width="8" height="5" fill="none" stroke="var(--blue)" stroke-width="1.6"/>
        <rect x="10" y="11" width="2" height="2" fill="var(--blue)"/>
        <rect x="14" y="11" width="2" height="2" fill="var(--blue)"/>
        <rect x="10" y="15" width="2" height="2" fill="var(--blue)"/>
        <rect x="14" y="15" width="2" height="2" fill="var(--blue)"/>
      </svg>
      416 555 0143
    </span>
  </div>

</div>
</body>
</html>
```